I need a business card designed using the logo provided either vertical or horizontal......Harbourline Property Group is an Australian based real estate company that caters for the upper end of the market so the design of the business card "must reflect" the companies image!!
Colour combinations are optional but "must be realistic" and must be able to be accurately useable CMYK colours.
Please consider that any colours used "must be able to be used" and be suitable in following designs for "pull out banner signs" and "real estate signs".
The colours and the font in the attached designs are for example and other combinations are encouraged.
Target Market(s)
The High End of the Australian real estate market
Industry/Entity Type
Business
Contact Information for Business Card
Logo - Business Name - Director + Licensed Real Estate Agent - Mobile Number (Cell Phone) - Business Number - Fax - Email Address - Web address
Requirements
Must have
- Designs and colours (CMYK) that can easily be interpreted by an Australian printer.
Nice to have
- Some alternative ideas on colour and font..........the ones provided are ok and have been provided as an example but I am looking for alternative ideas
Should not have
- Loud, overly bright colours. Designs that do not reflect the professional standards of the business.
- Designs that look good on a computer monitor but can not be re-created on a printing press.............this is most important when it comes to shading etc.

```html
<!DOCTYPE html>
<html lang="en">
<head>
<meta charset="UTF-8">
<title>Harbourline Property Group – Business Card</title>
<link href="https://fonts.googleapis.com/css2?family=Source+Sans+3:wght@400;600&display=swap" rel="stylesheet">
<style>
  :root {
    --backdrop: #2a2522;
    --card: #0d0d0d;
    --gold: #c9962a;
    --gold-light: #e0b24a;
    --silver: #b9b9b9;
    --white: #f1f1f1;
    --divider: #2c2c2c;
  }
  * { margin: 0; padding: 0; box-sizing: border-box; }
  html, body {
    width: 1200px; height: 844px; overflow: hidden;
    background: var(--backdrop);
    font-family: "Source Sans 3", "Myriad Pro", Arial, sans-serif;
  }
  .canvas {
    position: relative; width: 1200px; height: 844px;
    display: flex; align-items: center; justify-content: center; gap: 60px;
  }
  .card {
    width: 525px; height: 300px;
    background: var(--card);
    position: relative;
    box-shadow: 0 14px 30px rgba(0,0,0,.5);
  }
  /* Front: brand + contact details */
  .card--front { display: flex; }
  .brand-block {
    width: 47%;
    display: flex; flex-direction: column; align-items: center; justify-content: center;
    gap: 14px;
    border-right: 1px solid var(--divider);
    margin: 30px 0;
  }
  .brand-mark { width: 22px; height: 22px; background: var(--gold); }
  .brand-name {
    color: var(--white); font-weight: 600; font-size: 21px;
    text-transform: uppercase; letter-spacing: 2px; text-align: center; line-height: 1.25;
  }
  .contact-block {
    flex: 1; padding: 46px 26px 0 24px;
    color: var(--gold); font-size: 14.5px; line-height: 1.35;
  }
  .person-name { color: var(--gold-light); font-size: 22px; line-height: 1.1; }
  .person-title { font-size: 14px; margin-bottom: 16px; }
  .address { margin-bottom: 16px; }
  .contact-line .label { color: var(--white); display: inline-block; width: 20px; }

  /* Back: brand only */
  .card--back {
    display: flex; flex-direction: column; align-items: center; justify-content: center; gap: 16px;
  }
  .card--back .brand-mark { background: var(--silver); width: 26px; height: 26px; }
  .card--back .brand-name { color: var(--silver); font-size: 26px; }
</style>
</head>
<body>
  <main class="canvas">
    <section class="card card--front" aria-label="Business card front">
      <div class="brand-block">
        <span class="brand-mark" aria-hidden="true"></span>
        <p class="brand-name">Harbourline<br>Property Group</p>
      </div>
      <div class="contact-block">
        <p class="person-name">Daniel Whitford</p>
        <p class="person-title">Managing Director</p>
        <p class="address">48 Quayside Drive<br>Sydney NSW 2000</p>
        <p class="contact-line"><span class="label">T:</span> 044-987 654 321</p>
        <p class="contact-line"><span class="label">E:</span> info@harbourline.com.au</p>
        <p class="contact-line"><span class="label">W:</span> www.harbourlinegroup.com</p>
      </div>
    </section>

    <section class="card card--back" aria-label="Business card back">
      <span class="brand-mark" aria-hidden="true"></span>
      <p class="brand-name">Harbourline<br>Property Group</p>
    </section>
  </main>
</body>
</html>
```